Brovanek Data Yellow rose letterhead

I have a new logo for my company but in its current form it is too large to be used on letterhead or as a email signature. I need to have the designer use elements from the current logo and create something close to the original but more suited for smaller items.
Updates

I just uploaded a copy of our logo that does not have the weathered affect. Thanks

Reason: More time for revisions

Industry/Entity Type

It Company

Requirements
Must have
• The design must maintain the visual effect of the current logo. It needs to include the yellow rose and the name of the company.
Nice to have
• It would be nice to maintain the stamp theme and incorporate my name, address, phone, email. etc.

```html
<!DOCTYPE html>
<html lang="en">
<head>
<meta charset="utf-8">
<title>Brovanek Data Letterhead</title>
<link href="https://fonts.googleapis.com/css2?family=Arimo:wght@400;700&display=swap" rel="stylesheet">
<style>
  :root {
    --backdrop: #b9b9b9;
    --paper: #ffffff;
    --earth: #5a4b43;
    --teal: #3cb2ae;
    --gold: #f2c230;
    --rose-pale: #fdf1d2;
    --rose-mist: #fbe6b4;
    --ink: #5a4b43;
  }
  * { margin: 0; padding: 0; box-sizing: border-box; }
  html, body {
    width: 848px; height: 1200px; overflow: hidden;
    background: var(--backdrop);
    font-family: "Arimo", Arial, sans-serif;
  }
  .letterhead {
    position: absolute; left: 108px; top: 152px;
    width: 632px; height: 895px;
    background: var(--paper);
    overflow: hidden;
  }
  .header-band {
    position: absolute; left: 0; top: 0; width: 100%; height: 76px;
    background: var(--earth);
  }
  .header-rule { position: absolute; left: 0; width: 100%; }
  .header-rule.gold { top: 76px; height: 3px; background: var(--gold); }
  .header-rule.teal { top: 79px; height: 2px; background: var(--teal); }
  .brand-mark {
    position: absolute; left: 14px; top: 8px;
    width: 106px; height: 106px; border-radius: 50%;
    background: radial-gradient(circle at 45% 40%, #fde27a, var(--gold) 70%);
  }
  .brand-name {
    position: absolute; left: 171px; top: 19px;
    width: 290px; white-space: nowrap;
    font-size: 28px; font-weight: 700; color: var(--teal);
    letter-spacing: 4.6px; line-height: 1;
  }
  .brand-tagline {
    position: absolute; left: 172px; top: 52px;
    width: 300px; white-space: nowrap;
    font-size: 16px; font-weight: 400; color: #ffffff;
    letter-spacing: 5.6px; line-height: 1;
  }
  .rose-watermark {
    position: absolute; left: -40px; top: 420px;
    width: 460px; height: 470px; border-radius: 50%;
    background: radial-gradient(ellipse at 45% 45%, var(--rose-mist) 0%, var(--rose-pale) 55%, rgba(253,241,210,0) 75%);
  }
  .contact-block {
    position: absolute; right: 25px; top: 788px;
    text-align: right; color: var(--ink);
    font-size: 13.5px; line-height: 18px; font-style: normal;
  }
  .contact-block .contact-name { font-weight: 700; font-size: 15px; }
  .footer-band { position: absolute; left: 0; bottom: 0; }
</style>
</head>
<body>
  <div class="letterhead">
    <div class="rose-watermark" role="img" aria-label="Large faint yellow rose decoration"></div>

    <header>
      <div class="header-band"></div>
      <div class="header-rule gold"></div>
      <div class="header-rule teal"></div>
      <div class="brand-mark" role="img" aria-label="Yellow rose emblem"></div>
      <div class="brand-name">Brovanek Data</div>
      <div class="brand-tagline">SMART DATA SYSTEMS</div>
    </header>

    <address class="contact-block">
      <div class="contact-name">Mara Linwood, PhD</div>
      <div>218 NW Cedar Ridge Way, Ste 1140</div>
      <div>Pine Hollow, TX 75901</div>
      <div>mara@brovanek-data.com</div>
      <div>1-800-555-0147</div>
    </address>

    <svg class="footer-band" width="632" height="24" viewBox="0 0 632 24" aria-hidden="true">
      <polygon points="0,2 408,2 430,24 0,24" fill="var(--earth)"/>
      <polyline points="0,1 409,1 431,24" fill="none" stroke="var(--gold)" stroke-width="2"/>
    </svg>
  </div>
</body>
</html>
```